Online business manager needs a website

I need a website designed and then coded. I am an online business manager serving a number of different industries providing administrative support to existing small businesses and helping solo practitioners get their new business up and running.

I didn't have a logo formally designed but have been using the attached avatar and wouldn't mind something that incorporated that.

The business doesn't have an official name, so I've just been using my name Lena Morvath, Online Business Manager or Lena Morvath, OBM. I've attached two documents that I have made previously for an example of content.

I would prefer the final site be in Wordpress.

Requirements
Must have
• A way to contact me, testimonials, list of services

```html
<!DOCTYPE html>
<html lang="en">
<head>
<meta charset="utf-8">
<title>Lena Morvath, OBM</title>
<link href="https://fonts.googleapis.com/css2?family=Montserrat:wght@500;600;700&family=Manrope:wght@400;500&display=swap" rel="stylesheet">
<style>
:root{
  --purple:#4a1486;
  --purple-deep:#3d0f73;
  --lavender:#e0d8ea;
  --ink:#222;
  --body:#444;
  --dark:#000;
  --panel:#1c1c1e;
  --white:#fff;
}
*{box-sizing:border-box;margin:0;padding:0}
html,body{width:1200px;height:4747px;overflow:hidden}
body{position:relative;background:var(--white);font-family:"Manrope",sans-serif;color:var(--body)}
.abs{position:absolute}
h1,h2,h3,.brand,.nav,.btn{font-family:"Montserrat",sans-serif}
.brand{color:var(--purple);font-weight:600;font-size:32px;line-height:41px;text-align:center;text-transform:uppercase;white-space:nowrap}
.nav{display:flex;gap:30px;font-size:16px;font-weight:500;color:var(--ink);text-transform:uppercase}
.nav .active{color:var(--purple)}
.btn{display:inline-block;background:var(--purple);color:var(--white);font-weight:600;font-size:23px;border-radius:40px;text-align:center;text-transform:uppercase}
.section-title{color:var(--purple);font-weight:600;font-size:33px;text-transform:uppercase;text-align:center;width:1200px;left:0}
.photo{background:linear-gradient(135deg,#c9ccd2,#8c929c 50%,#5b6270)}
.card{background:var(--white);box-shadow:0 2px 10px rgba(0,0,0,.22)}
.card .photo{height:276px}
.card h3{color:var(--purple);font-weight:600;font-size:25px;line-height:39px;text-transform:uppercase}
.card ul{list-style:none;font-size:23px;color:var(--ink)}
.card li{line-height:50px;padding-left:30px;position:relative}
.card li::before{content:"";position:absolute;left:4px;top:20px;width:10px;height:10px;border-top:3px solid var(--ink);border-right:3px solid var(--ink);transform:rotate(45deg)}
.rate{background:var(--white);box-shadow:0 2px 10px rgba(0,0,0,.18);text-align:center}
.rate-head{background:var(--purple);color:var(--white);font-family:"Montserrat",sans-serif;font-weight:500;font-size:20px;height:117px;padding-top:24px;line-height:40px}
.rate-body{font-size:22px;line-height:50px;color:var(--ink);padding:20px 4px 0}
.rate-foot{position:absolute;left:0;right:0;bottom:0;height:84px;background:var(--purple);color:var(--white);font-size:23px;line-height:34px;padding-top:8px;clip-path:polygon(0 0,100% 0,100% 100%,8% 100%)}
.contact-label{font-family:"Montserrat",sans-serif;font-weight:600;font-size:22px;color:var(--white)}
.contact-value{font-size:21px;color:var(--white)}
.icon-circle{width:68px;height:68px;border-radius:50%;background:var(--white);display:flex;align-items:center;justify-content:center}
.social{width:56px;height:56px;border-radius:50%;background:var(--purple);display:flex;align-items:center;justify-content:center}
</style>
</head>
<body>

<header>
  <div class="brand abs" style="left:37px;top:14px;width:360px">Lena Morvath,<br>OBM</div>
  <nav class="nav abs" style="left:514px;top:47px">
    <span class="active">Home</span><span>About Me</span><span>Services</span><span>Testimonials</span><span>Contact Me</span>
  </nav>
</header>

<section class="hero">
  <div class="photo abs" role="img" aria-label="Two colleagues talking in a bright office" style="left:0;top:105px;width:1200px;height:640px;background:linear-gradient(100deg,#e8e9ec,#b9bcc3 35%,#7d818a 60%,#d6d7da)"></div>
  <svg class="abs" style="left:0;top:700px" width="1200" height="50" viewBox="0 0 1200 50"><polygon points="0,40 1200,0 1200,8 0,50" fill="#4a1486"/><polygon points="0,50 1200,8 1200,50" fill="#fff"/></svg>
  <div class="abs" style="left:600px;top:200px;width:600px;height:415px;background:var(--panel);text-align:right;padding:80px 112px 0 0">
    <h2 style="color:#fff;font-weight:500;font-size:37px;line-height:44px">WELCOME TO</h2>
    <h1 style="color:#fff;font-weight:600;font-size:52px;line-height:80px;margin-top:10px;white-space:nowrap">LENA MORVATH</h1>
    <span class="btn" style="width:265px;height:64px;line-height:64px;margin-top:22px">Get Started</span>
  </div>
</section>

<section class="about">
  <h2 class="abs" style="left:200px;top:878px;width:360px;text-align:right;color:var(--purple);font-weight:600;font-size:33px">ABOUT US</h2>
  <p class="abs" style="left:95px;top:940px;width:465px;text-align:right;font-size:19px;line-height:41.5px;color:var(--ink)">Hi! I'm so excited that you have chosen to explore my portfolio. Helping businesses achieve their goals is my passion, and I'm thrilled that with my assistance you will have more time for your own passion project. I thrive while working independently, which means you can be</p>
  <span class="btn abs" style="left:336px;top:1217px;width:226px;height:60px;line-height:54px;border:4px solid #b9a6d6">Read More</span>
  <div class="photo abs" role="img" aria-label="Portrait photo of Lena Morvath against a starry purple background" style="left:588px;top:812px;width:510px;height:510px;border-radius:50%;border:6px solid var(--purple);background:radial-gradient(circle at 55% 45%,#d9b9a0,#8b6a7a 45%,#2a2a6e 80%)"></div>
</section>

<section class="services">
  <h2 class="section-title abs" style="top:1406px">Services</h2>

  <div class="card abs" style="left:111px;top:1502px;width:475px;height:590px">
    <div class="photo" role="img" aria-label="Hands typing on a laptop with floating app icons"></div>
    <div style="padding:44px 0 0 96px">
      <h3>Virtual Assistance</h3>
      <ul style="margin-top:6px"><li>Calendar Management</li><li>Email Management</li><li>Light Graphic Design</li><li>Data Entry</li></ul>
    </div>
  </div>

  <div class="card abs" style="left:608px;top:1502px;width:476px;height:595px">
    <div class="photo" role="img" aria-label="Person using a phone with social media icons" style="background:linear-gradient(135deg,#5a5e66,#8d9098 50%,#c0a88a)"></div>
    <div style="padding:14px 0 0 62px">
      <h3>Social Media &amp; Content<br>Management</h3>
      <ul style="margin-top:4px"><li>Content Repurposing</li><li>Graphics Creation</li><li>Audiogram Creation</li><li>Search Engine Optimization</li></ul>
    </div>
  </div>

  <div class="card abs" style="left:111px;top:2126px;width:475px;height:590px">
    <div class="photo" role="img" aria-label="Laptop keyboard with glowing folder icons" style="background:linear-gradient(135deg,#3c4a55,#6b8a90 50%,#aeb7b9)"></div>
    <div style="padding:40px 0 0 80px">
      <h3>Finance Management</h3>
      <ul style="margin-top:6px;padding-left:16px"><li>Create Invoices Track</li><li>Receivables Analyze</li><li>Expenses Year</li><li>Over Year Analytics</li></ul>
    </div>
  </div>

  <div class="card abs" style="left:608px;top:2126px;width:476px;height:595px">
    <div class="photo" role="img" aria-label="Hand ticking a checklist beside a laptop" style="background:linear-gradient(135deg,#2e4a66,#55789a 50%,#a9b5bf)"></div>
    <div style="padding:44px 0 0 72px">
      <h3>Business Management</h3>
      <ul style="margin-top:6px;margin-left:-42px"><li>Creation of Operating Procedures</li><li>Review of Website Strategy</li><li>Reporting and Analytics</li><li>Project Management</li></ul>
    </div>
  </div>
</section>

<section class="testimonials">
  <svg class="abs" style="left:0;top:2805px" width="1200" height="782" viewBox="0 0 1200 782"><polygon points="0,0 1200,33 1200,782 0,782" fill="#e0d8ea"/></svg>
  <h2 class="section-title abs" style="top:2906px">Testimonials</h2>
  <div class="photo abs" role="img" aria-label="Portrait photo of client Dana R." style="left:480px;top:2995px;width:240px;height:240px;border-radius:50%;border:6px solid #8a6bb8;background:radial-gradient(circle,#b98a6a,#6d7a4a 70%)"></div>
  <svg class="abs" style="left:88px;top:3284px" width="20" height="30" viewBox="0 0 20 30"><polyline points="16,3 4,15 16,27" fill="none" stroke="#4a1486" stroke-width="3.5"/></svg>
  <svg class="abs" style="left:1088px;top:3284px" width="20" height="30" viewBox="0 0 20 30"><polyline points="4,3 16,15 4,27" fill="none" stroke="#4a1486" stroke-width="3.5"/></svg>
  <h3 class="abs" style="left:0;width:1200px;top:3276px;text-align:center;font-family:'Montserrat',sans-serif;color:var(--purple);font-weight:600;font-size:24px">DANA R. OWNER, NORTHGATE ROOFING</h3>
  <p class="abs" style="left:160px;top:3330px;width:880px;text-align:center;font-size:23px;line-height:50px;color:var(--ink)">When it became apparent that a project would take more time than I had, Lena stepped up to take on the required research. She was thorough and timely; able to meet a last-minute 12-hour deadline. I would highly recommend Lena to assist with your next project.</p>
</section>

<section class="rates">
  <h2 class="section-title abs" style="top:3677px">Rates and Packages</h2>
  <div class="rate abs" style="left:120px;top:3760px;width:230px;height:400px">
    <div class="rate-head">$40<br>HOURLY RATE</div>
    <div class="rate-body" style="padding-top:50px">For clients<br>needing only<br>occasional help</div>
  </div>
  <div class="rate abs" style="left:362px;top:3760px;width:231px;height:400px">
    <div class="rate-head">$700<br>20 HOURS/MONTH</div>
    <div class="rate-body">Includes one 15<br>minute meeting per<br>week</div>
    <div class="rate-foot">Responses within<br>72 hours</div>
  </div>
  <div class="rate abs" style="left:604px;top:3760px;width:231px;height:400px">
    <div class="rate-head">$1300<br>40 HOURS/MONTH</div>
    <div class="rate-body">Includes one 30<br>minute meeting per<br>week</div>
    <div class="rate-foot">Responses within<br>48 hours</div>
  </div>
  <div class="rate abs" style="left:847px;top:3760px;width:233px;height:400px">
    <div class="rate-head">$2400<br>80 HOURS/MONTH</div>
    <div class="rate-body">Includes one 60<br>minute meeting per<br>week</div>
    <div class="rate-foot">Responses within<br>24 hours</div>
  </div>
</section>

<footer>
  <div class="abs" style="left:0;top:4320px;width:1200px;height:427px;background:var(--dark)"></div>
  <svg class="abs" style="left:110px;top:4255px" width="1006" height="182" viewBox="0 0 1006 182"><polygon points="24,0 1006,0 982,182 0,182" fill="#4a1486"/></svg>

  <div class="icon-circle abs" style="left:252px;top:4308px">
    <svg width="34" height="34" viewBox="0 0 24 24"><path d="M6.6 10.8a15.1 15.1 0 0 0 6.6 6.6l2.2-2.2a1 1 0 0 1 1-.25 11.4 11.4 0 0 0 3.6.57 1 1 0 0 1 1 1V20a1 1 0 0 1-1 1A17 17 0 0 1 3 4a1 1 0 0 1 1-1h3.5a1 1 0 0 1 1 1c0 1.25.2 2.45.57 3.57a1 1 0 0 1-.25 1z" fill="#4a1486"/></svg>
  </div>
  <div class="contact-label abs" style="left:340px;top:4300px">CALL US:</div>
  <div class="contact-value abs" style="left:340px;top:4334px">555.210.4487</div>

  <div class="icon-circle abs" style="left:610px;top:4308px">
    <svg width="38" height="28" viewBox="0 0 38 28"><rect x="2" y="2" width="34" height="24" rx="2" fill="none" stroke="#4a1486" stroke-width="3"/><polyline points="2,3 19,16 36,3" fill="none" stroke="#4a1486" stroke-width="3"/><line x1="2" y1="26" x2="14" y2="13" stroke="#4a1486" stroke-width="2.5"/><line x1="36" y1="26" x2="24" y2="13" stroke="#4a1486" stroke-width="2.5"/></svg>
  </div>
  <div class="contact-label abs" style="left:698px;top:4300px">MAIL US:</div>
  <div class="contact-value abs" style="left:698px;top:4334px">lena.morvath@mailbox.example</div>

  <div class="brand abs" style="left:400px;top:4452px;width:400px;color:#fff">Lena Morvath,<br>OBM</div>
  <nav class="nav abs" style="left:0;width:1200px;top:4554px;justify-content:center;color:#fff;gap:29px">
    <span>Home</span><span>About Me</span><span>Services</span><span>Testimonials</span><span>Contact Me</span>
  </nav>
  <div class="abs" style="left:0;width:1200px;top:4610px;text-align:center;font-size:18px;color:#fff">@2023 COPYRIGHTS &nbsp;&nbsp;&nbsp;<b style="font-family:'Montserrat',sans-serif;font-weight:600">LENA MORVATH, OBM</b>&nbsp;&nbsp;&nbsp;&nbsp; I &nbsp;&nbsp;&nbsp;&nbsp;ALL RIGHTS RESERVED.</div>
  <div class="social abs" style="left:530px;top:4676px" aria-label="Social profile">
    <svg width="26" height="26" viewBox="0 0 26 26"><circle cx="13" cy="9" r="5" fill="#fff"/><path d="M3 24c0-6 4.5-9 10-9s10 3 10 9z" fill="#fff"/></svg>
  </div>
  <div class="social abs" style="left:613px;top:4676px" aria-label="Share">
    <svg width="26" height="26" viewBox="0 0 26 26"><circle cx="6" cy="13" r="3.5" fill="#fff"/><circle cx="20" cy="6" r="3.5" fill="#fff"/><circle cx="20" cy="20" r="3.5" fill="#fff"/><line x1="6" y1="13" x2="20" y2="6" stroke="#fff" stroke-width="2"/><line x1="6" y1="13" x2="20" y2="20" stroke="#fff" stroke-width="2"/></svg>
  </div>
</footer>

</body>
</html>
```